New layout on letterheads, businesscards, flyers, brochures etc.

Dear Sir,
We would like to change our layout a bit. We would like to have the same look on everything we make and still keep our logo. We would like some suggestions suitable for a company like ours, where solar systems, heat pumps and LED lighting is reflected. We like our blue colour in our logo (#009ddf) and some of the black reflected in our solar panels and we like the solar cell (almost square with soft corners). We like soft lines, clean look and reflecting expensive solar panels from the very best distributors (QX, Halvorenti, Kestrel Arcwave etc.). We want a light, soft, exclusive and expensive look to it all. We need this for business cards, letterhead/bottom, flyers, brochures and stickers etc.
Thank you in advance.

Tavurn
Lindvej 28 B
8215 Brandholt
Denmark

info@tavurn.dk
www.tavurn.dk

```html
<!DOCTYPE html>
<html lang="en">
<head>
<meta charset="utf-8">
<title>Tavurn – Business Card</title>
<link rel="stylesheet" href="https://fonts.googleapis.com/css2?family=Ubuntu:ital,wght@0,400;0,500;0,700;1,400&display=swap">
<style>
  :root {
    --brand-blue: #1e9ddb;
    --panel-black: #3a3a3c;
    --text-dark: #3d3d3f;
    --logo-grey: #a7a9ac;
    --paper: #ffffff;
  }
  * { margin: 0; padding: 0; box-sizing: border-box; }
  html, body {
    width: 1200px;
    height: 777px;
    overflow: hidden;
    background: var(--paper);
  }
  .card {
    position: relative;
    width: 1200px;
    height: 777px;
    background: var(--paper);
    font-family: "Ubuntu", sans-serif;
    color: var(--text-dark);
  }
  .edge-band {
    position: absolute;
    left: 0;
    width: 1200px;
    height: 22px;
    display: flex;
  }
  .edge-band--top { top: 0; }
  .edge-band--bottom { bottom: 0; }
  .edge-band__blue { width: 916px; background: var(--brand-blue); }
  .edge-band__black { flex: 1; background: var(--panel-black); }

  .website {
    position: absolute;
    right: 67px;
    top: 72px;
    font-size: 33px;
    font-style: italic;
    color: var(--brand-blue);
    letter-spacing: 0.3px;
  }

  .brand {
    position: absolute;
    left: 46px;
    top: 208px;
    display: flex;
    align-items: center;
    gap: 22px;
  }
  .brand__cell {
    width: 84px;
    height: 84px;
    border-radius: 18px;
    background: var(--brand-blue);
  }
  .brand__name {
    font-size: 72px;
    font-weight: 700;
    color: var(--logo-grey);
    letter-spacing: 1px;
    line-height: 1;
  }

  .person {
    position: absolute;
    left: 486px;
    top: 226px;
  }
  .person__name {
    font-size: 40px;
    font-weight: 400;
    color: var(--brand-blue);
    line-height: 1;
    letter-spacing: 0.3px;
  }
  .person__role {
    margin-top: 24px;
    font-size: 40px;
    font-style: italic;
    color: var(--text-dark);
    line-height: 1;
  }

  .contact {
    position: absolute;
    left: 486px;
    top: 393px;
    font-size: 36px;
    line-height: 58px;
    color: var(--text-dark);
  }
  .contact__phone { font-size: 41px; }
  .contact__email { font-size: 39px; }
</style>
</head>
<body>
  <div class="card">
    <div class="edge-band edge-band--top">
      <div class="edge-band__blue"></div>
      <div class="edge-band__black"></div>
    </div>

    <div class="website">www.tavurn.dk</div>

    <div class="brand">
      <div class="brand__cell"></div>
      <div class="brand__name">Tavurn</div>
    </div>

    <div class="person">
      <div class="person__name">Anders Holm Vestergaard</div>
      <div class="person__role">Technical Manager and Partner</div>
    </div>

    <div class="contact">
      <div class="contact__address">Lindvej 28 B, 8215 Brandholt,</div>
      <div class="contact__address">Denmark.</div>
      <div class="contact__phone">P +45 61 38 52 90</div>
      <div class="contact__phone">M +45 40 17 93 26</div>
      <div class="contact__email">ahv@tavurn.dk</div>
    </div>

    <div class="edge-band edge-band--bottom">
      <div class="edge-band__blue"></div>
      <div class="edge-band__black"></div>
    </div>
  </div>
</body>
</html>
```